GivingGavelHub Website Redesign

I'm looking to give our website a new look and feel with better graphics/images and that is focused on conversions.
www.givinggavelhub.example. The content can stay the same. Im looking for a new hero section with maybe a call to auction form to create an auction by asking for the following information: Event Name, Event Benefits, Country, Time zone and currency.
Our goal is to show that we can host online auctions, mobile auctions and live in-person auction. The content does not need to change on the site. We just need sections or illustrations that represent those features. It would also be good to have a sections that will segment our users into the following categories: Nonprofits/Charities, Schools/Education, Businesses, Government Agency, Individual.
The following pages need to be updated:
https://www.givinggavelhub.example/
https://www.givinggavelhub.example/online-bidding-features
https://www.givinggavelhub.example/online-bidding-experience
https://www.givinggavelhub.example/about
https://www.givinggavelhub.example/pricing
Updates
This project would cover the following 4 pages:
https://www.givinggavelhub.example

```html
<!DOCTYPE html>
<html lang="en">
<head>
<meta charset="utf-8">
<title>GivingGavelHub — Online Auction Platform</title>
<link href="https://fonts.googleapis.com/css2?family=Roboto:wght@400;500;700;900&display=swap" rel="stylesheet">
<style>
:root{
  --blue:#1f74d6;
  --blue-deep:#0d4fa3;
  --blue-bright:#3b8ff0;
  --blue-card:#175cb4;
  --blue-light:#3f93ec;
  --ink:#222;
  --muted:#666;
  --line:#dcdcdc;
  --dark:#151515;
  --white:#fff;
}
*{margin:0;padding:0;box-sizing:border-box}
html,body{width:1200px;height:3953px;overflow:hidden}
body{font-family:"Roboto",Arial,sans-serif;color:var(--ink);background:var(--white);position:relative}
.page{position:relative;width:1200px;height:3953px}
.abs{position:absolute}
.brand{font-family:"Roboto",Arial,sans-serif;font-weight:500;letter-spacing:-.5px;color:var(--blue)}
.brand-dot{display:inline-block;width:36px;height:36px;border-radius:50%;background:var(--blue);vertical-align:middle;margin-right:10px}

/* header */
.top-rule{top:0;left:0;width:1200px;height:4px;background:var(--blue)}
.header{top:4px;left:0;width:1200px;height:114px;border-bottom:1px solid #e7e7e7}
.header .brand{position:absolute;left:110px;top:38px;font-size:30px}
.btn-touch{position:absolute;left:952px;top:20px;width:137px;height:42px;border-radius:21px;background:var(--blue);color:#fff;font-size:15px;font-weight:500;display:flex;align-items:center;justify-content:center}
.nav{position:absolute;right:111px;top:80px;display:flex;gap:30px;font-size:15px;color:#555}

/* hero */
.hero{top:118px;left:0;width:1200px;height:542px;background:linear-gradient(120deg,#1a65c9 0%,#2a83e8 55%,#3c93f0 100%)}
.hero h1{position:absolute;left:110px;top:135px;width:480px;color:#fff;font-size:44px;line-height:54px;font-weight:900;text-transform:uppercase;letter-spacing:.3px}
.btn-outline{border:2px solid #fff;color:#fff;border-radius:24px;font-size:15px;font-weight:500;display:flex;align-items:center;justify-content:center}
.hero .btn-outline{position:absolute;left:110px;top:384px;width:156px;height:44px}
.auction-form{top:226px;left:613px;width:476px;height:521px;background:#fff;border-radius:4px;box-shadow:0 6px 24px rgba(0,0,0,.15)}
.auction-form .form-mark{position:absolute;left:218px;top:34px;width:40px;height:40px;border-radius:50%;background:var(--blue)}
.auction-form h2{position:absolute;top:88px;width:100%;text-align:center;font-size:31px;font-weight:700;color:#222}
.field{position:absolute;left:45px;width:386px;height:40px;border:1px solid var(--line);border-radius:3px;font-size:12px;color:#666;padding-left:24px;display:flex;align-items:center}
.btn-submit{position:absolute;left:45px;top:446px;width:386px;height:40px;border-radius:4px;background:linear-gradient(#2d8ae8,#0e56b0);color:#fff;font-size:14px;font-weight:700;display:flex;align-items:center;justify-content:center}

/* section headings */
.section-title{left:0;width:1200px;text-align:center;font-size:40px;font-weight:700;text-transform:uppercase;color:#222}

/* we host */
.host-col{top:915px;width:300px;text-align:center}
.host-art{width:240px;height:230px;margin:0 auto;border-radius:12px;background:linear-gradient(160deg,#e4efff,#bcd6f7)}
.host-col h3{margin-top:40px;font-size:20px;font-weight:500;color:#222}
.host-col p{margin-top:14px;font-size:12px;line-height:25px;color:#666}

/* categories */
.categories{top:1397px;left:0;width:1200px;height:686px;background:linear-gradient(135deg,#0f5bb8,#1a6fd0 50%,#0f5bb8)}
.categories .section-title{color:#fff;top:80px}
.cat-card{width:310px;height:196px;background:#fff;display:flex;flex-direction:column;align-items:center;justify-content:center;gap:22px;font-size:16px;color:#333}
.cat-card svg{width:76px;height:70px;stroke:var(--blue);fill:none;stroke-width:2.5;stroke-linecap:round;stroke-linejoin:round}
.cat-card.more{font-size:24px;font-weight:700;color:var(--blue);gap:14px}
.cat-card.more svg{width:50px;height:50px}

/* benefits */
.benefit{top:2254px;width:472px;height:493px;color:#fff;text-align:center;border-radius:3px;overflow:hidden}
.benefit .photo{height:258px}
.benefit h3{margin-top:30px;font-size:20px;font-weight:700}
.benefit p{margin:14px auto 0;width:360px;font-size:15px;line-height:27px}
.benefit .btn-outline{margin:20px auto 0;width:156px;height:44px;font-size:14px}
.btn-solid{top:2791px;left:523px;width:154px;height:43px;border-radius:22px;background:var(--blue);color:#fff;font-size:15px;font-weight:500;display:flex;align-items:center;justify-content:center}

/* partners */
.partners{top:3020px;left:150px;width:900px;display:flex;justify-content:space-between;align-items:center}
.partner{display:flex;align-items:center;gap:10px;font-size:20px;font-weight:500;color:#555}
.partner i{display:inline-block;width:28px;height:28px;background:#c9c9c9;border-radius:50%}

/* download */
.dark-band{top:3484px;left:0;width:1200px;height:469px;background:var(--dark)}
.download{top:3262px;left:137px;width:1063px;height:428px;background:#fff;border-radius:214px 0 0 214px}
.download-mark{top:3340px;left:170px;width:360px;height:270px;display:flex;align-items:center;justify-content:center;font-size:40px;font-weight:700;color:var(--blue)}
.download h2{position:absolute;left:460px;top:68px;font-size:40px;line-height:54px;font-weight:700;color:#222;text-transform:uppercase}
.download p{position:absolute;left:462px;top:193px;width:460px;font-size:15px;line-height:27px;color:#555}
.download .btn-cta{position:absolute;left:462px;top:301px;width:292px;height:43px;border-radius:22px;background:var(--blue);color:#fff;font-size:15px;font-weight:700;display:flex;align-items:center;justify-content:center}

/* footer */
.footer-brand{top:3745px;left:0;width:1200px;text-align:center;font-size:32px;color:#fff}
.footer-brand .brand-dot{background:#fff}
.footer-nav{top:3848px;left:0;width:1200px;display:flex;justify-content:center;gap:30px;font-size:15px;color:#fff}
.copyright{top:3903px;left:0;width:1200px;text-align:center;font-size:12px;color:#fff}
</style>
</head>
<body>
<div class="page">
  <div class="abs top-rule"></div>
  <header class="abs header">
    <div class="brand"><span class="brand-dot"></span>GivingGavelHub</div>
    <div class="btn-touch">Get In Touch</div>
    <nav class="nav"><span>How It Works</span><span>About</span><span>Blog</span><span>Silent Auctions</span><span>Browse Auctions</span></nav>
  </header>

  <section class="abs hero">
    <h1>You’ve just found the easiest online auction platform to use, period.</h1>
    <div class="btn-outline">Build An Action</div>
  </section>

  <form class="abs auction-form">
    <div class="form-mark"></div>
    <h2>CREATE AN AUCTION</h2>
    <div class="field" style="top:157px">Event Name</div>
    <div class="field" style="top:214px">Event Benefits</div>
    <div class="field" style="top:272px">Country</div>
    <div class="field" style="top:330px">Time zone</div>
    <div class="field" style="top:388px">Currency</div>
    <div class="btn-submit">Submit Here</div>
  </form>

  <h2 class="abs section-title" style="top:822px">We Host</h2>
  <div class="abs host-col" style="left:107px">
    <div class="host-art" role="img" aria-label="Illustration of an online auction with a phone and bid button"></div>
    <h3>Online Auctions</h3>
    <p>Lorem Ipsum is simply dummy text of the printing and typesetting industry. Lorem Ipsum has been the industry's standard</p>
  </div>
  <div class="abs host-col" style="left:450px">
    <div class="host-art" role="img" aria-label="Illustration of a hand holding a phone with bid tags"></div>
    <h3>Mobile Auctions</h3>
    <p>Lorem Ipsum is simply dummy text of the printing and typesetting industry. Lorem Ipsum has been the industry's standard</p>
  </div>
  <div class="abs host-col" style="left:793px">
    <div class="host-art" role="img" aria-label="Illustration of an auctioneer and a bidding audience"></div>
    <h3>Live In-Person Auctions</h3>
    <p>Lorem Ipsum is simply dummy text of the printing and typesetting industry. Lorem Ipsum has been the industry's standard</p>
  </div>

  <section class="abs categories">
    <h2 class="abs section-title">Our Categories</h2>
    <div class="abs cat-card" style="left:111px;top:178px">
      <svg viewBox="0 0 76 70"><path d="M38 64 C10 44 4 30 4 20 A16 16 0 0 1 38 14 A16 16 0 0 1 72 20 C72 30 66 44 38 64Z"/><path d="M18 36 l14 12 M26 30 l14 12"/></svg>
      Nonprofits/Charities
    </div>
    <div class="abs cat-card" style="left:445px;top:178px">
      <svg viewBox="0 0 76 70"><path d="M4 24 L38 10 L72 24 L38 38Z"/><path d="M18 30 v16 c10 8 30 8 40 0 v-16"/><path d="M66 27 v20"/><circle cx="66" cy="51" r="3"/></svg>
      Schools/Education
    </div>
    <div class="abs cat-card" style="left:779px;top:178px">
      <svg viewBox="0 0 76 70"><rect x="6" y="18" width="64" height="44" rx="3"/><path d="M28 18 v-8 h20 v8 M6 36 h64"/><rect x="32" y="32" width="12" height="8"/></svg>
      Businesses
    </div>
    <div class="abs cat-card" style="left:111px;top:393px">
      <svg viewBox="0 0 76 70"><path d="M8 22 L38 8 L68 22Z M10 22 h56 M14 28 v24 M26 28 v24 M38 28 v24 M50 28 v24 M62 28 v24 M8 56 h60 M4 62 h68"/></svg>
      Government Agencies
    </div>
    <div class="abs cat-card" style="left:445px;top:393px">
      <svg viewBox="0 0 76 70"><circle cx="22" cy="16" r="8"/><circle cx="54" cy="16" r="8"/><circle cx="38" cy="30" r="9"/><path d="M10 44 c0-10 6-16 12-16 M66 44 c0-10-6-16-12-16 M22 64 v-10 c0-8 8-14 16-14 s16 6 16 14 v10"/></svg>
      Individuals
    </div>
    <div class="abs cat-card more" style="left:779px;top:393px">
      <svg viewBox="0 0 50 50"><circle cx="25" cy="25" r="22"/><path d="M25 14 v22 M14 25 h22"/></svg>
      View More
    </div>
  </section>

  <h2 class="abs section-title" style="top:2147px">Spend less time. Make more money.</h2>
  <article class="abs benefit" style="left:111px;background:var(--blue-card)">
    <div class="photo" role="img" aria-label="Photo of an auctioneer at a live event with bidders raising paddles" style="background:linear-gradient(135deg,#8a7a6a,#4a4038)"></div>
    <h3>Quickly create, design and manage auctions</h3>
    <p>You are only 5 minutes away from having your auction built and ready for items. We took the pain and confusion out of getting started.</p>
    <div class="btn-outline">Build An Action</div>
  </article>
  <article class="abs benefit" style="left:617px;background:var(--blue-light)">
    <div class="photo" role="img" aria-label="Photo of two excited people looking at a phone" style="background:linear-gradient(135deg,#6b6258,#2f2a27)"></div>
    <h3>More money goes directly to your cause</h3>
    <p>You can accept cash, checks, bank transfers, or credit cards. It’s your money, collect it on your own terms.</p>
    <div class="btn-outline">Collect More Money</div>
  </article>
  <div class="abs btn-solid">View More</div>

  <h2 class="abs section-title" style="top:2921px">You're in good company</h2>
  <div class="abs partners" style="top:3060px">
    <div class="partner"><i></i>Harborview Club</div>
    <div class="partner"><i></i>Lakeshore Institute</div>
    <div class="partner"><i></i>Riverton Ironclads</div>
    <div class="partner"><i></i>Maplewood College</div>
  </div>

  <div class="abs dark-band"></div>
  <section class="abs download">
    <h2>Download the auction<br>profit blueprintTM</h2>
    <p>Learn the 4 tools BIG Organizations use to skyrocket their auction profits! Stop leaving thousands of dollars on the table by following this Step-By-Step Guide.</p>
    <div class="btn-cta">HELP ME RAISE MORE MONEY</div>
  </section>
  <div class="abs download-mark brand">GivingGavelHub</div>

  <div class="abs footer-brand brand" style="color:#fff"><span class="brand-dot"></span>GivingGavelHub</div>
  <nav class="abs footer-nav"><span>Home</span><span>How It Works</span><span>About Us</span><span>Blog</span><span>Silent Auctions</span><span>Browse Auctions</span></nav>
  <div class="abs copyright">© 2023 GivingGavelHub LLC | All Rights Reserved</div>
</div>
</body>
</html>
```